Church Website with Home Page and Member Sermon Library

I am in need of an updated design for our church website. This will include 4 pages (outlined below). We are a conservative, evangelical, Christian church. The site should be modern and clean, while still reflecting our conservative values. I already have a logo for our church, and I want the site to incorporate the logo, and match the logo/branding. Stock photos are allowed if needed, but I have uploaded some images of our church and would prefer those images to be used if possible. Any stock photos used should not include any people in the photos (scenery, nature, buildings, animals, etc. are fine).

The site will need 4 pages: Home, Support Us (Donate), Login, and Recording Library.

Page 1: Home
The home page should include the following sections:

- Navigation: Should include links to each section of the home page plus a "listen live" link which will take the user to a live-streaming site and a "support us" link which will take the user to a support/donate page.

- Announcements: Can be either a banner or some other design, but there needs to be some way for us to post announcements for visitors to see. I'm open for creative ideas in this section, but would like it not to take up a lot of room on the page.

- About Us: Should include address, service times (see attached document), and information about the church.

- Pastor Bio: A section that introduces our pastor and gives a short bio about our pastor. Would like this section to include a picture of our pastor. Somewhere in this section I would like to include this Bible reference: "And I will give you pastors according to mine heart, which shall feed you with knowledge and understanding. Jer 3:15 LPW"

- Articles of Faith (What We Believe): This should include several sub-sections each with a heading, body, and possibly 1 or more scripture references. I have attached a document to the brief that includes our articles of faith. Feel free to be creative with this section in how you lay these out and format them.

- Support Us: A small section that explains what kind of support someone can give and a link to a donation page. The link can say something like "Support Us" or "Donate Now".

- Contact form: A contact form that allows the visitor to send us a message. The contact form should ask for name, email, phone, and message.

- Footer: A footer that will be displayed on all pages of the site. This should include at a minimum a link to the home page (or a link to each individual section in the home page if you prefer), a link to "listen live", a link to "support us", a link to "contact us" (or you can put the contact form directly in the footer if you prefer), the address, and a "member login" link.

Page 2: Support Us
The donation page should include a form the visitor can fill out to make a donation. We will embed a third party form later. For this design, please just mock out the design with a basic form asking for name, phone, and email.

Page 3: Login
The recording library (detailed below) will require members to login with a shared numeric code before accessing the page. We need a design for a login screen. The screen should include navigation/footer just like all other pages, but the body of the login page will consist only of a form that asks the user to enter the access code and then a "login" button.

Page 4: Recording Library

The library page is a member-only page that will require a shared, numeric pass code to access. On this page, members will be able to access a filterable list of past sermons. The page by default should display most recent sermons, but should also include a search form that allows the member to filter the sermon list to find a particular sermon. The search form should allow the user to select a filter type (e.g. Speaker name, date, event, etc.) and type in a value to search. They should be able to add multiple filters and remove filters that have been added. Each sermon that is displayed in the result list should include basic information such as title, date, speaker, tags, etc. along with a download icon, and an embedded audio player where they can click a play button to stream it on-demand. Each sermon should also have clickable tags associated with it that can be used to find related sermons.
Updates

I have uploaded several images of our church. Feel free to incorporate these into your design if possible.

Target Market(s)

Church Members

Industry/Entity Type

Religion

Number of Pages Required

4 page

Font styles to use
Sans Serif

Colors

Designer to choose colors to be used in the design.

Requirements
Must have
• Must incorporate the logo (attached)
Nice to have
• Would like the design to incorporate pictures of our church (attached) instead of stock photos if possible.
Should not have
• Please avoid an overly cluttered design. Stock photos used should not include any people in the photos.

```html
<!DOCTYPE html>
<html lang="en">
<head>
<meta charset="utf-8">
<title>Cedar Grove Church</title>
<link href="https://fonts.googleapis.com/css2?family=Marcellus&family=Raleway:ital,wght@0,400;0,500;0,600;0,700;1,500&display=swap" rel="stylesheet">
<style>
:root{
  --green:#7aab66;
  --green-soft:#8fba7c;
  --green-dark:#2f4a25;
  --cyan:#00b7da;
  --ink:#333;
  --muted:#555;
  --white:#fff;
  --foot-bar:#eef0ec;
}
*{margin:0;padding:0;box-sizing:border-box}
html,body{width:1200px;height:4043px;overflow:hidden}
body{position:relative;background:var(--white);font-family:"Raleway",sans-serif;color:var(--ink)}
.abs{position:absolute}
.serif{font-family:"Marcellus",serif;font-weight:400}

/* header */
.site-header{left:0;top:0;width:1200px;height:83px;background:var(--white)}
.brand{left:130px;top:18px;color:var(--green);text-align:center;line-height:1}
.brand .top{font-size:12px;letter-spacing:9px}
.brand .main{font-size:34px;letter-spacing:2px;margin:2px 0}
.brand .sub{font-size:10px;letter-spacing:9px}
.main-nav{left:385px;top:33px;display:flex;font-size:13px;font-weight:500;color:var(--ink)}
.main-nav a{color:inherit;text-decoration:none}
.main-nav .sep{color:var(--green);margin:0 32px}
.main-nav .active{color:var(--cyan)}
.live-btn{left:920px;top:24px;width:157px;height:36px;border-radius:18px;background:var(--green);color:#fff;font-size:12px;font-weight:600;display:flex;align-items:center;justify-content:center;letter-spacing:.5px}

/* hero */
.hero{left:0;top:83px;width:1200px;height:700px;background:linear-gradient(180deg,#5f8fc4 0%,#9ebfdf 35%,#dfe8ef 55%,#a5503c 62%,#8b4a36 72%,#7f9a49 82%,#9fb05c 100%)}
.hero-curve{left:0;top:620px;width:1200px;height:170px}
.welcome-box{left:106px;top:302px;width:485px;height:153px;border:2px solid var(--green)}
.welcome-tag{left:256px;top:283px;width:196px;height:34px;background:var(--green);color:#fff;font-size:21px;letter-spacing:3px;display:flex;align-items:center;justify-content:center}
.welcome-title{left:106px;top:322px;width:485px;text-align:center;color:var(--green);font-size:46px;line-height:50px;letter-spacing:1px}
.welcome-title span{display:block;color:#3f6a33}
.donate-pill{left:252px;top:435px;width:195px;height:42px;border-radius:21px;background:var(--cyan);color:#fff;font-size:15px;font-weight:600;display:flex;align-items:center;justify-content:center}

/* announcement */
.announce-frame{left:122px;top:815px;width:958px;height:207px}
.announce-title{left:132px;top:866px;width:955px;text-align:center;color:#fff;font-size:33px;letter-spacing:2px}
.announce-lead{left:132px;top:924px;width:955px;text-align:center;color:#fff;font-size:15px;font-weight:700}
.announce-body{left:132px;top:952px;width:955px;text-align:center;color:#fff;font-size:13px}

/* about */
.about-art{left:146px;top:1095px;width:378px;height:562px}
.eyebrow{color:var(--green-dark);letter-spacing:3px;font-size:20px}
.about-eyebrow{left:600px;top:1158px;color:#3f6a33}
.about-title{left:600px;top:1182px;color:var(--green);font-size:46px;letter-spacing:1px}
.rule{height:2px;background:var(--green)}
.about-rule{left:602px;top:1245px;width:97px}
.about-copy{left:600px;top:1270px;width:520px;font-size:15.5px;line-height:29px;color:var(--muted)}
.about-copy p+p{margin-top:6px}
.timing-label{left:601px;top:1480px;color:var(--green);font-size:17px;font-weight:600}
.timing{left:601px;top:1517px;width:520px;display:grid;grid-template-columns:275px 245px;row-gap:17px;font-size:13px;font-weight:600;color:#222}

/* pastor */
.pastor{left:0;top:1703px;width:1200px;height:562px;background:linear-gradient(180deg,#00bcdd 0%,#1fb9d8 60%,#5bbfd0 100%)}
.pastor-title{left:132px;top:1812px;color:#fff;font-size:44px;letter-spacing:1px}
.pastor-rule{left:133px;top:1867px;width:96px;background:#fff}
.pastor-copy{left:132px;top:1907px;width:480px;color:#fff;font-size:15px;font-weight:500;line-height:23px}
.pastor-copy p+p{margin-top:6px}
.pastor-quote{left:133px;top:2060px;width:480px;color:#fff;font-size:16px;font-weight:500;font-style:italic;line-height:23px}
.pastor-ref{left:136px;top:2118px;color:#fff;font-size:16px;font-weight:600}
.pastor-frame{left:667px;top:1798px;width:370px;height:373px;border:1.5px solid #ccf3fa}
.pastor-corner{left:920px;top:2060px;width:120px;height:116px;background:#fff}
.pastor-photo{left:680px;top:1812px;width:347px;height:352px;background:linear-gradient(160deg,#b9a58b 0%,#6c5d4e 40%,#2b2a2c 75%,#3a3530 100%)}

/* articles */
.articles-tag{left:476px;top:2328px;width:236px;height:33px;background:var(--green);color:#fff;font-size:18px;letter-spacing:3px;display:flex;align-items:center;justify-content:center}
.articles-title{left:0;top:2366px;width:1200px;text-align:center;color:var(--green);font-size:42px;letter-spacing:2px}
.articles-rule{left:550px;top:2425px;width:90px}
.articles-frame{left:132px;top:2498px;width:435px;height:460px;border:2px solid var(--green)}
.articles-photo{left:147px;top:2513px;width:436px;height:457px;background:linear-gradient(180deg,#3d79c8 0%,#9bbde3 35%,#e4e9ee 60%,#d6d7d3 80%,#4c6a3a 100%)}
.faith-item{left:647px;width:465px}
.faith-item h3{font-family:"Marcellus",serif;font-weight:400;color:var(--green-dark);font-size:22px;letter-spacing:3px;margin-bottom:10px}
.faith-item p{font-size:14px;line-height:27px;color:var(--muted)}
.faith-one{top:2507px}
.faith-two{top:2705px}
.faith-two p{font-size:13px}
.faith-divider{left:647px;top:2677px;width:465px;height:1px;background:#d8dcd4}
.learn-btn{left:647px;top:2918px;width:194px;height:44px;border-radius:22px;background:var(--cyan);color:#fff;font-size:16px;font-weight:500;display:flex;align-items:center;justify-content:center}

/* contact */
.contact{left:0;top:3082px;width:1200px;height:573px;background:linear-gradient(180deg,#7aab66 0%,#7fad6b 62%,#6f9a5d 80%,#8ab678 100%)}
.contact-eyebrow{left:0;top:3155px;width:1200px;text-align:center;color:#fff;font-size:16px;letter-spacing:3px}
.contact-title{left:0;top:3170px;width:1200px;text-align:center;color:#fff;font-size:43px;letter-spacing:2px}
.field{background:#fff;color:#777;font-size:14px;padding:0 20px;display:flex;align-items:center;border-radius:2px}
.f1{left:208px;top:3264px;width:390px;height:53px}
.f2{left:608px;top:3264px;width:390px;height:53px}
.f3{left:208px;top:3330px;width:390px;height:53px}
.f4{left:608px;top:3330px;width:390px;height:53px}
.f5{left:208px;top:3395px;width:790px;height:100px;align-items:flex-start;padding-top:18px}
.send-btn{left:507px;top:3518px;width:196px;height:46px;border-radius:23px;background:var(--green-dark);color:#fff;font-size:15px;font-weight:500;display:flex;align-items:center;justify-content:center}

/* footer */
.foot-brand{left:138px;top:3738px;color:var(--green);text-align:center;line-height:1}
.foot-col-line{width:1px;background:#e2e6df;top:3660px;height:325px}
.foot-head{color:var(--green);font-size:15px;letter-spacing:2px;border-left:2px solid var(--cyan);padding-left:20px;font-weight:500}
.foot-links{left:426px;top:3775px;font-size:13px;color:var(--muted);line-height:30.5px;list-style:none}
.foot-text{left:620px;top:3775px;width:210px;font-size:13px;line-height:19px;color:var(--muted)}
.foot-btn{left:617px;top:3845px;width:134px;height:30px;border-radius:15px;background:var(--green);color:#fff;font-size:11px;display:flex;align-items:center;justify-content:center}
.contact-row{left:870px;display:flex;align-items:center;gap:13px;font-size:12px;color:#333;line-height:16px}
.icon{width:34px;height:34px;border-radius:50%;background:var(--green);display:flex;align-items:center;justify-content:center;flex:none}
.copyright{left:0;top:3985px;width:1200px;height:58px;background:var(--foot-bar);display:flex;align-items:center;justify-content:center;font-size:12px;color:#777}
</style>
</head>
<body>

<header class="site-header abs">
  <div class="brand abs serif">
    <div class="top">CEDAR</div>
    <div class="main">GROVE</div>
    <div class="sub">CHURCH</div>
  </div>
  <nav class="main-nav abs">
    <a class="active" href="#">HOME</a><span class="sep">|</span>
    <a href="#">ABOUT CHURCH</a><span class="sep">|</span>
    <a href="#">LIBRARY</a><span class="sep">|</span>
    <a href="#">DONATION</a>
  </nav>
  <a class="live-btn abs">LIVE-STREAMING</a>
</header>

<section class="hero abs" role="img" aria-label="Photo of the red-brick church with a white steeple under a blue sky"></section>
<svg class="hero-curve abs" viewBox="0 0 1200 170" preserveAspectRatio="none" aria-hidden="true">
  <path d="M0 70 C200 135 420 80 520 95 C560 100 585 120 597 150 C609 120 635 100 680 95 C790 80 1000 135 1200 60 L1200 170 L0 170 Z" fill="#fff"/>
  <path d="M0 48 C200 120 420 65 520 80 C560 85 585 105 597 135 C609 105 635 85 680 80 C790 65 1000 120 1200 40" fill="none" stroke="#7aab66" stroke-width="3"/>
  <path d="M0 80 C200 145 420 90 520 105 C560 110 585 130 597 158 C609 130 635 110 680 105 C790 90 1000 145 1200 72" fill="none" stroke="#7aab66" stroke-width="2"/>
</svg>
<div class="welcome-box abs"></div>
<div class="welcome-tag abs serif">WELCOME TO</div>
<h1 class="welcome-title abs serif">CEDAR GROVE<span>CHURCH</span></h1>
<a class="donate-pill abs">DONATE NOW</a>

<svg class="announce-frame abs" viewBox="0 0 958 207" aria-hidden="true">
  <path d="M60 1 H956 V140 C956 178 930 205 890 205 H1 V60 C1 28 28 1 60 1 Z" fill="none" stroke="#7aab66" stroke-width="2"/>
  <path d="M70 10 H948 V140 C948 172 925 196 890 196 H10 V70 C10 36 36 10 70 10 Z" fill="#7aab66"/>
</svg>
<h2 class="announce-title abs serif">ANNOUNCEMENT</h2>
<p class="announce-lead abs">LOREM IPSUM DOLOR SIT AMET CONSECTETUR ADIPISCING</p>
<p class="announce-body abs">magna aliqua. Ut enim ad minim veniam, quis nostrud exercitation Allamco laboris nisi ut aliquip ex ea</p>

<svg class="about-art abs" viewBox="0 0 378 562" role="img" aria-label="Photo of the church steeple and brick building against a blue sky">
  <defs>
    <linearGradient id="skyBrick" x1="0" y1="0" x2="0" y2="1">
      <stop offset="0" stop-color="#1a63c6"/><stop offset="0.45" stop-color="#5f9de0"/>
      <stop offset="0.7" stop-color="#9b4a37"/><stop offset="1" stop-color="#7a3b2b"/>
    </linearGradient>
  </defs>
  <path d="M189 2 C160 40 110 70 40 100 C10 112 2 140 2 170 V380 C2 420 15 445 60 470 C120 505 165 530 189 560 C213 530 258 505 318 470 C363 445 376 420 376 380 V170 C376 140 368 112 338 100 C268 70 218 40 189 2 Z" fill="none" stroke="#00b7da" stroke-width="2.5"/>
  <path d="M189 16 C162 52 115 80 48 108 C20 120 13 145 13 172 V378 C13 414 25 436 66 460 C124 494 167 518 189 545 C211 518 254 494 312 460 C353 436 365 414 365 378 V172 C365 145 358 120 330 108 C263 80 216 52 189 16 Z" fill="url(#skyBrick)"/>
</svg>
<div class="about-eyebrow abs eyebrow serif">CEDAR GROVE</div>
<h2 class="about-title abs serif">ABOUT OUR CHURCH</h2>
<div class="about-rule abs rule"></div>
<div class="about-copy abs">
  <p>Lorem ipsum dolor sit amet, consectetur adipiscing elit, sed do eiusmod tempor incididunt ut labore et dolore magna aliqua. Ut enim ad minim veniam, quis nostrud exercitation</p>
  <p>Allamco laboris nisi ut aliquip ex ea commodo consequat. Duis aute irure dolor in reprehenderit in voluptate velit esse cillum dolore eu fugiat nulla pariatur. Excepteur sint occaecat cupidatat</p>
</div>
<div class="timing-label abs">SERVICE TIMING:</div>
<div class="timing abs">
  <span>Wednesday Night Service: 7:30 PM</span><span>Sunday Morning Service: 11:00 AM</span>
  <span>Sunday School: 10:00 AM</span><span>Sunday Night Service: 5:30 PM</span>
</div>

<section class="pastor abs"></section>
<h2 class="pastor-title abs serif">PASTOR BIO</h2>
<div class="pastor-rule abs rule"></div>
<div class="pastor-copy abs">
  <p>Lorem ipsum dolor sit amet, consectetur adipiscing elit, sed do eiusmod tempor incididunt ut labore et dolore magna aliqua. Ut enim ad minim veniam, quis nostrud exercitation</p>
  <p>Allamco laboris nisi ut aliquip ex ea commodo consequat. Duis aute irure dolor in reprehenderit in voluptate velit esse</p>
</div>
<blockquote class="pastor-quote abs">“And I will give you pastors according to mine heart, which shall feed you with knowledge and understanding”</blockquote>
<div class="pastor-ref abs">Jer 3:15 LPW</div>
<div class="pastor-frame abs"></div>
<div class="pastor-corner abs"></div>
<div class="pastor-photo abs" role="img" aria-label="Portrait of the pastor holding an open Bible inside the sanctuary"></div>

<div class="articles-tag abs serif">CEDAR GROVE</div>
<h2 class="articles-title abs serif">ARTICLES OF FAITH</h2>
<div class="articles-rule abs rule"></div>
<div class="articles-frame abs"></div>
<div class="articles-photo abs" role="img" aria-label="Photo of a white church with a tall spire under a cloudy blue sky"></div>
<article class="faith-item faith-one abs">
  <h3>THE GOD HEAD.</h3>
  <p>We believe in the God head bodily, known as the Divine Trinity. This body consist of God the father, Jesus Christ, his only begotten son and the redeemer of the world, and of the Holy Ghost, The third person of the Divine Trinity.</p>
</article>
<div class="faith-divider abs"></div>
<article class="faith-item faith-two abs">
  <h3>FULL SALVATION</h3>
  <p>We believe that Salvation is received only when a person comes to the realization that he or she is lost and separated from God and becomes full of godly sorrow, confessing their sins and true repentance, believing in the shed blood of the Lord Jesus Christ as the only sacrifice for sins. Through the blood of Christ we have:</p>
</article>
<a class="learn-btn abs">LEARN MORE</a>

<section class="contact abs" role="img" aria-label="Faded green-toned photo of the church building"></section>
<div class="contact-eyebrow abs serif">GET IN TOUCH</div>
<h2 class="contact-title abs serif">CONTACT US</h2>
<div class="field f1 abs">First Name</div>
<div class="field f2 abs">Last Name</div>
<div class="field f3 abs">Email address</div>
<div class="field f4 abs">Phone</div>
<div class="field f5 abs">Message</div>
<a class="send-btn abs">SEND MESSAGE</a>

<footer>
  <div class="foot-brand abs serif brand" style="left:185px;top:3747px">
    <div class="top">CEDAR</div>
    <div class="main">GROVE</div>
    <div class="sub">CHURCH</div>
  </div>
  <div class="foot-col-line abs" style="left:397px"></div>
  <div class="foot-col-line abs" style="left:597px"></div>
  <div class="foot-col-line abs" style="left:852px"></div>
  <div class="foot-head abs" style="left:400px;top:3735px">NAVIGATION</div>
  <ul class="foot-links abs">
    <li>About Us</li><li>Library</li><li>Donation</li><li>Live Streaming</li><li>Contact Us</li>
  </ul>
  <div class="foot-head abs" style="left:598px;top:3735px">DONATION</div>
  <p class="foot-text abs">Lorem ipsum dolor sit amet, consectetur adipiscing elit, sed do eiusmod tempor inci</p>
  <a class="foot-btn abs">DONATE NOW</a>
  <div class="foot-head abs" style="left:853px;top:3735px">CONTACT US</div>
  <div class="contact-row abs" style="top:3765px">
    <span class="icon"><svg width="16" height="18" viewBox="0 0 16 18"><path d="M8 1a6 6 0 0 0-6 6c0 4.5 6 10 6 10s6-5.5 6-10a6 6 0 0 0-6-6z" fill="#fff"/><circle cx="8" cy="7" r="2.3" fill="#7aab66"/></svg></span>
    <span>28 Willow Lane, Suite 4, Riverton,<br>OH 45002 USA</span>
  </div>
  <div class="contact-row abs" style="top:3813px">
    <span class="icon"><svg width="18" height="13" viewBox="0 0 18 13"><rect x="1" y="1" width="16" height="11" fill="none" stroke="#fff" stroke-width="1.6"/><path d="M1 1l8 6 8-6" fill="none" stroke="#fff" stroke-width="1.6"/></svg></span>
    <span>hello@cedargrovechurch.org</span>
  </div>
  <div class="contact-row abs" style="top:3862px">
    <span class="icon"><svg width="16" height="16" viewBox="0 0 16 16"><path d="M3 1l3 3-1.6 2a9 9 0 0 0 5.6 5.6L12 10l3 3-2 2C7 15 1 9 1 3z" fill="#fff"/></svg></span>
    <span>(+123) 555 0142</span>
  </div>
  <div class="copyright abs">© 2023 Cedar Grove Church. All Rights Reserved</div>
</footer>

</body>
</html>
```